Front and back cover design for skincare marketing materials

Thank you for showing an interest in my project.
Project Details.

I require a front and back cover for our marketing materials.
·       Front Cover size: 105 mm W x 150 mm H.
·       Back Cover size:  105 mm W x 150 mm H.
·       It must include these two colors. You can use a third color if you wish.
1.     #DBA09D
2.     #FFFFFF
 
Front Cover
·      The front cover will have a faded image of the Kakadu Plum branch and fruit. There are two image files, KP_image-1.jpg and kp_image-2.jpeg. You can use both images, just a portion of them, or source alternative royalty-free images of Kakadu Plum that may better fit the design. These two files have been uploaded.
 
The front cover wording.
Top of the front cover.
a.     The title of the image. “Kakadu Plum”
b.     The brand name, “Vellora Skincare”. The file brand_name.ai uploaded.
 
Bottom of the front cover- Designer's choice of font.
The bottom of the front cover contains three lines of text in the following order.  
1.     Australian Native Ingredients
2.     100% Natural · Organic · Wild-harvested
3.     Australian-Made Premium Skincare
 
Back Cover
·      Back Cover wording.The back cover contains the following words "grown by nature" in white (#FFFFFF) of font Italianno (font_file.ttf) with a background color of #DBA09D as seen in the sample box (sample_box.pdf) right-side panel
 
Please provide one file for the front cover and a separate file for the back cover.
All the elements of the files must be editable.
 
Do NOT use the Curve function on the files, as the text must remain editable/changeable.
 
All assets/resources/files, including fonts not supplied by us but used by the designer, must be named and provided with the finished design.
Updates

Slow to provide project details.

Target Market(s)

Beauty-minded Asian consumers between the ages of 32 and 75 who take a proactive approach to maintaining younger-looking skin. Those who already know the danger of skin damage caused by skincare containing harsh chemicals choose effective natural/organic solutions to meet their skincare needs. Those who wish a more radiant glow and youthful appearance to their skin. Usually, a two-income middle to high-income bracket couples with a mindset for health and beauty.

Industry/Entity Type

beauty

Font styles to use
Other font styles liked:
• I will provide a font file and a brand name file.

Requirements
Must have
• You must use the two colors provided on the product box. The designer may use a third color.
Nice to have
• some gold colour

```html
<!DOCTYPE html>
<html lang="en">
<head>
<meta charset="utf-8">
<title>Vellora Skincare – Kakadu Plum Covers</title>
<link rel="stylesheet" href="https://fonts.googleapis.com/css2?family=Pinyon+Script&family=Italianno&family=Montserrat:wght@400&family=Poppins:wght@500;600&display=swap">
<style>
  :root {
    --backdrop: #e7e7e7;
    --brand-pink: #dba09d;
    --deep-pink: #c9827f;
    --white: #ffffff;
    --ink: #141212;
    --cream: #fbf1e6;
    --leaf-green: #b9c46a;
    --badge: #231f20;
  }
  * { margin: 0; padding: 0; box-sizing: border-box; }
  html, body {
    width: 1200px; height: 1094px; overflow: hidden;
    background: var(--backdrop);
  }
  .cover {
    position: absolute; top: 198px;
    width: 490px; height: 698px; overflow: hidden;
    background: var(--brand-pink);
  }
  .cover--front { left: 82px; }
  .cover--back { left: 628px; }

  .front-photo {
    position: absolute; inset: 0 0 180px 0;
    background:
      radial-gradient(ellipse 55% 45% at 78% 28%, rgba(185,196,106,0.9), rgba(185,196,106,0) 70%),
      linear-gradient(160deg, var(--cream) 0%, #f4d6c4 45%, rgba(219,160,157,0) 100%);
  }
  .brand-name {
    position: absolute; left: 32px; top: 92px;
    font-family: "Poppins", sans-serif; font-weight: 500;
    font-size: 24px; letter-spacing: 3px;
    color: var(--deep-pink);
  }
  .product-title {
    position: absolute; left: 0; right: 0; top: 320px;
    text-align: center;
    font-family: "Pinyon Script", cursive;
    font-size: 118px; line-height: 1;
    color: var(--ink);
  }
  .product-subtitle {
    position: absolute; left: 0; right: 0; top: 442px;
    text-align: center;
    font-family: "Montserrat", sans-serif; font-weight: 400;
    font-size: 68px; line-height: 1; letter-spacing: 22px;
    padding-left: 22px;
    color: var(--white);
  }
  .category-badge {
    position: absolute; left: 102px; top: 512px;
    width: 286px; height: 22px; border-radius: 3px;
    background: var(--badge);
    font-family: "Poppins", sans-serif; font-weight: 600;
    font-size: 14px; line-height: 22px; letter-spacing: 3px;
    text-align: center; color: var(--white);
  }
  .features { position: absolute; left: 0; right: 0; top: 556px; height: 116px; }
  .feature {
    position: absolute; top: 0; width: 150px; margin-left: -75px;
    text-align: center;
    font-family: "Poppins", sans-serif; font-weight: 500;
    font-size: 14.5px; line-height: 17px; color: var(--ink);
  }
  .feature svg { display: block; margin: 0 auto 8px; }
  .feature:nth-child(1) { left: 98px; }
  .feature:nth-child(2) { left: 243px; }
  .feature:nth-child(3) { left: 390px; }
  .feature-divider {
    position: absolute; top: 2px; width: 1px; height: 112px;
    background: rgba(255,255,255,0.6);
  }

  .tagline {
    position: absolute; left: 245px; top: 349px;
    transform: translate(-50%, -50%) rotate(-90deg);
    white-space: nowrap;
    font-family: "Italianno", cursive;
    font-size: 112px; line-height: 1;
    color: var(--white);
  }
</style>
</head>
<body>
  <section class="cover cover--front">
    <div class="front-photo" role="img" aria-label="Faded photograph of a Kakadu plum branch with green fruit"></div>
    <div class="brand-name">Vellora Skincare</div>
    <h1 class="product-title">Kakadu</h1>
    <div class="product-subtitle">PLUM</div>
    <div class="category-badge">AUSTRALIAN SUPERFOODS</div>
    <div class="features">
      <div class="feature">
        <svg width="44" height="44" viewBox="0 0 44 44"><circle cx="22" cy="22" r="20.5" fill="none" stroke="#fff" stroke-width="2"/><circle cx="22" cy="22" r="12" fill="#fff"/></svg>
        Australian<br>Native<br>Ingredients
      </div>
      <div class="feature">
        <svg width="44" height="44" viewBox="0 0 44 44"><circle cx="22" cy="22" r="20.5" fill="none" stroke="#fff" stroke-width="2"/><circle cx="22" cy="22" r="12" fill="#fff"/></svg>
        100% Natural<br>Organic<br>Wild-harvested
      </div>
      <div class="feature">
        <svg width="44" height="44" viewBox="0 0 44 44"><circle cx="22" cy="22" r="20.5" fill="none" stroke="#fff" stroke-width="2"/><circle cx="22" cy="22" r="12" fill="#fff"/></svg>
        Australian-Made<br>Premium<br>Skincare
      </div>
      <span class="feature-divider" style="left:173px"></span>
      <span class="feature-divider" style="left:316px"></span>
    </div>
  </section>

  <section class="cover cover--back">
    <p class="tagline">grown by nature</p>
  </section>
</body>
</html>
```